Cat-products company needs smart, yet endearing, business card

We need a business card design for a new, but up-and-running, business based in Honolulu, Hawaii. The business is Purrnest Nook Co. Our first product is the most environmentally-friendly cat grass kit ever seen on the planet. Future products, currently in the R&D phase, will include a variety of exciting cat scratchers. We also do consulting work to help apartment-dwellers make their home more cat-friendly and, in the future, plan on doing full, custom installs of structure to create high walkways for cats.

Target Market(s)

Middle-aged, apartment-dwelling, middle-class workers who own 1 or more cats and who dote on them.

Industry/Entity Type

Pet Care

Contact Information for Business Card

A striking, professional, yet warm and friendly design is what we're after.

Font styles to use
Serif
Sans Serif
Other font styles liked:
• Comfortaa

Colors

Designer to choose colors to be used in the design.

Requirements
Must have
• The company logo: (see attachment)
• The company name: Purrnest Nook Co
• The web address: www.purrnestnookco.com
• Email: support@purrnestnookco.com
• Phone: +1 (808) 571 6023
• Update (Fri Jun 30 3017 7:45pm Hawaii Time) I would like, is possible, uploaded picture of the cat grass kit on the back of the card with some text along the lines of: Purrnest Nook Co - Maker Of The Leafiest Feline Sprout Set Yet
Nice to have
• A cat picture, cartoon, real or silhouette that illustrates cats in action and/or relaxing; ie using the apartment space to live, play and relax in and being well-contented.
• Most of the website is done in the font: Comfortaa. It might be nice to continue using this for brand consistency.
Should not have
• Hard-to-read fonts.

```html
<!DOCTYPE html>
<html lang="en">
<head>
<meta charset="utf-8">
<title>Purrnest Nook Co – Business Card</title>
<link rel="stylesheet" href="https://fonts.googleapis.com/css2?family=Fredoka:wght@600&family=Questrial&display=swap">
<style>
  :root {
    --backdrop: #2b2b2b;
    --paper: #f2f2f2;
    --cocoa: #54312b;
    --amber: #f0ab00;
    --ink: #4a3b37;
    --white: #ffffff;
    --dot: #8a6a62;
  }
  * { margin: 0; padding: 0; box-sizing: border-box; }
  html, body { width: 1200px; height: 960px; overflow: hidden; }
  body {
    background: var(--backdrop);
    position: relative;
    font-family: "Questrial", "Century Gothic", sans-serif;
  }
  .card {
    position: absolute;
    width: 600px;
    height: 342px;
    border-radius: 22px;
    overflow: hidden;
  }
  .card-front { left: 314px; top: 114px; background: var(--paper); }
  .card-back { left: 311px; top: 473px; background: var(--cocoa); }

  .brand-name {
    font-family: "Fredoka", "Comfortaa", sans-serif;
    font-weight: 600;
    line-height: 1;
  }
  .card-front .brand-name {
    position: absolute;
    left: 36px;
    top: 40px;
    width: 220px;
    font-size: 40px;
    color: var(--amber);
  }
  .side-tab {
    position: absolute;
    left: -16px;
    top: 143px;
    width: 32px;
    height: 44px;
    border-radius: 50%;
    background: var(--amber);
  }
  .person-name {
    position: absolute;
    left: 39px;
    top: 144px;
    font-size: 21px;
    color: var(--ink);
    letter-spacing: 0.3px;
  }
  .person-role {
    position: absolute;
    left: 39px;
    top: 172px;
    font-size: 15px;
    color: var(--amber);
  }
  .address {
    position: absolute;
    left: 39px;
    top: 207px;
    font-size: 15px;
    line-height: 19px;
    color: var(--ink);
    font-style: normal;
  }
  .contact-list {
    position: absolute;
    left: 39px;
    top: 256px;
    list-style: none;
    font-size: 15px;
    line-height: 19px;
    color: var(--ink);
  }
  .contact-list li { display: flex; align-items: center; gap: 8px; }
  .contact-list svg { width: 13px; height: 13px; fill: var(--cocoa); flex: none; }

  .mark-panel {
    position: absolute;
    left: 312px;
    top: 100px;
    width: 236px;
    height: 230px;
    border-radius: 6px;
    background: var(--cocoa);
  }

  .social-dots {
    position: absolute;
    right: 16px;
    top: 18px;
    display: flex;
    gap: 2px;
  }
  .social-dots span {
    width: 22px; height: 22px; border-radius: 50%;
    background: var(--dot);
  }
  .back-mark {
    position: absolute;
    left: 262px;
    top: 78px;
    width: 76px;
    height: 76px;
    background: var(--white);
    border-radius: 4px;
  }
  .card-back .brand-name {
    position: absolute;
    left: 0;
    top: 186px;
    width: 100%;
    text-align: center;
    font-size: 44px;
    color: var(--amber);
  }
  .back-url {
    position: absolute;
    left: 0;
    top: 294px;
    width: 100%;
    text-align: center;
    font-size: 15px;
    letter-spacing: 4px;
    color: var(--white);
  }
</style>
</head>
<body>
  <section class="card card-front">
    <div class="brand-name">Purrnest Nook Co</div>
    <span class="side-tab"></span>
    <h1 class="person-name" style="font-weight:400">MAREN KEALOHA</h1>
    <p class="person-role">CEO/FOUNDER</p>
    <address class="address">4120 Lanai Vista Way<br>Honolulu, Hawaii 96815</address>
    <ul class="contact-list">
      <li>
        <svg viewBox="0 0 16 16" aria-hidden="true"><path d="M3.5 1l2.6 3.2-1.5 1.8c.8 1.9 2.4 3.5 4.3 4.3l1.8-1.5L14 11.5 12.5 14C6.8 14 2 9.2 2 3.5z"/></svg>
        +1 (808) 571 6023
      </li>
      <li>
        <svg viewBox="0 0 16 16" aria-hidden="true"><path d="M1 3h14v1.2L8 8.6 1 4.2zM1 5.6l7 4.4 7-4.4V13H1z"/></svg>
        support@purrnestnookco.com
      </li>
      <li>
        <svg viewBox="0 0 16 16" aria-hidden="true"><circle cx="8" cy="8" r="7"/></svg>
        www.purrnestnookco.com
      </li>
    </ul>
    <div class="mark-panel"></div>
  </section>

  <section class="card card-back">
    <div class="social-dots" aria-hidden="true"><span></span><span></span><span></span><span></span></div>
    <div class="back-mark"></div>
    <div class="brand-name">Purrnest Nook Co</div>
    <p class="back-url">www.purrnestnookco.com</p>
  </section>
</body>
</html>
```